Exciting opportunity to create logo and a label for our natural health brand.

About us

We are a customer centric health supplement brand who believes in natural medicine and high quality ingredients. We take a holistic approach to healthcare, with an eastern philosophy. We believe in being partners with our customers in their health care journey and are invested in their well being.

Our brand philosophy and values are attached (see Vorna philosophy.png). Our personality traits are:

- Natural
- Fresh
- Modern
- Balanced (in a holistic sense)

Task breakdown

1. Design a fresh feeling logo for us
- We want it to represent our values and high quality ingredients. We would like the quality of the product to be reflected in the branding and have a high end feel.
- Logo text must include Vorna Health Sciences
- We want the Vorna to be the focus of the logo (see uploaded image Vorna logo example.png)
The logo does not have to follow this layout, but we just want the Vorna to stand out. Feel free to use your creative license on this!

2. Create an attractive label to go on the supplement bottle
- The designs need to be eye catching, give a sense of high end ingredients and natural products and tie in with the logo to give a joined up feel.
- We are selling our products online and need them to really stand out from the competition.
- See examples of labels and packaging we like (1 -7 label design).

The initial label we would like you to design would be for our product Calm Drift. It is a product that assists in the management of Anxiety and stress. The label will appear on the bottle that holds the capsules for this supplement, see uploaded files (Example plain bottles.png). The bottles may be white as the picture shows or dark blue recyclable plastic or dark brown glass . We don't have the exact dimensions of the bottle yet, but I will follow up with these.

The label needs to include the following things:
1. The logo
2. The name of the product
3. The product is to help with the relief of Anxiety and Stress
4. Number of capsules the bottle contains
5. The back of the label should have
i) The ingredients
ii) Dosage
iii) Directions of use

Please use placeholder text where needed.

We look forward to seeing your design. Thank you.

```html
<!DOCTYPE html>
<html lang="en">
<head>
<meta charset="utf-8">
<title>Vorna Health Science – Calm Drift Label</title>
<link href="https://fonts.googleapis.com/css2?family=Barlow:wght@500;600&display=swap" rel="stylesheet">
<style>
  :root {
    --teal: #0f6e72;
    --paper: #ffffff;
    --backdrop: #f1f2f2;
    --botanical: #c9cfcd;
    --seam: #dfe2e2;
  }
  html, body {
    margin: 0;
    width: 1200px;
    height: 750px;
    overflow: hidden;
    background: var(--backdrop);
  }
  .canvas {
    position: relative;
    width: 1200px;
    height: 750px;
  }
  .label {
    position: absolute;
    left: 330px;
    top: 30px;
    width: 540px;
    height: 690px;
    font-family: "Barlow", "DIN Alternate", sans-serif;
  }
  .label svg { display: block; }
  .band { fill: var(--teal); }
  .label-body { fill: var(--paper); }
  .seam { stroke: var(--seam); stroke-width: 2; fill: none; }
  .brand-name {
    fill: var(--teal);
    font-weight: 600;
    font-size: 124px;
  }
  .brand-line {
    fill: var(--teal);
    font-weight: 600;
    font-size: 17px;
    letter-spacing: 13px;
  }
  .product-name {
    fill: var(--teal);
    font-weight: 600;
    font-size: 38px;
  }
  .product-claim {
    fill: var(--teal);
    font-weight: 500;
    font-size: 21px;
    letter-spacing: 2px;
  }
  .count-number {
    fill: var(--teal);
    font-weight: 600;
    font-size: 36px;
    letter-spacing: 2px;
  }
  .count-unit {
    fill: var(--teal);
    font-weight: 500;
    font-size: 25px;
    letter-spacing: 2px;
  }
</style>
</head>
<body>
<main class="canvas">
  <section class="label">
    <svg width="540" height="690" viewBox="0 0 540 690" xmlns="http://www.w3.org/2000/svg">
      <defs>
        <linearGradient id="botanical-tone" x1="0" y1="0" x2="1" y2="1">
          <stop offset="0" stop-color="var(--botanical)" stop-opacity="0.15"/>
          <stop offset="0.6" stop-color="var(--botanical)" stop-opacity="0.45"/>
          <stop offset="1" stop-color="var(--botanical)" stop-opacity="0.2"/>
        </linearGradient>
      </defs>

      <rect class="label-body" x="0" y="0" width="540" height="690"/>

      <path role="img" aria-label="Faint line drawing of a flowering herb sprig"
            d="M185 80 L540 80 L540 320 L200 320 Z" fill="url(#botanical-tone)"/>
      <path role="img" aria-label="Faint line drawing of a leafy herb branch"
            d="M180 445 L540 445 L540 650 L300 650 Z" fill="url(#botanical-tone)"/>

      <path class="band" d="M0 12 C140 0 260 0 540 12 L540 50 C360 28 200 22 0 24 Z"/>

      <text class="brand-name" x="270" y="222" text-anchor="middle">Vorna</text>
      <text class="brand-line" x="276" y="258" text-anchor="middle">HEALTH SCIENCE</text>

      <rect class="label-body" x="0" y="312" width="540" height="128"/>
      <line class="seam" x1="0" y1="312" x2="540" y2="312"/>
      <line class="seam" x1="0" y1="440" x2="540" y2="440"/>

      <text class="product-name" x="270" y="374" text-anchor="middle">Calm Drift</text>
      <text class="product-claim" x="270" y="404" text-anchor="middle">Reduce stress and anxiety naturally</text>

      <text class="count-number" x="270" y="598" text-anchor="middle">60</text>
      <text class="count-unit" x="270" y="626" text-anchor="middle">capsules</text>

      <path class="band" d="M0 633 C150 660 380 662 540 640 L540 660 C380 688 150 690 0 660 Z"/>
    </svg>
  </section>
</main>
</body>
</html>
```